Kestrel Facilities Business Card Design

We would now like to design business cards with the new Kestrel Facilities logo

Target Market(s)

Professional

Industry/Entity Type

Professional services

Contact Information for Business Card

Employee name, title, phone number, email address, corporate office address and logo.

Font styles to use
Sans Serif

Colors
0054AA
0677BA
7BADD7
CADEEF
E8F1F8

Requirements
Must have
• My logo
Should not have
• any other pictures or images besides my logo

```html
<!DOCTYPE html>
<html lang="en">
<head>
<meta charset="utf-8">
<title>Kestrel Facilities – Business Card</title>
<link href="https://fonts.googleapis.com/css2?family=Montserrat:wght@400;500;700&display=swap" rel="stylesheet">
<style>
  :root {
    --backdrop: #8c8c8c;
    --card: #ffffff;
    --brand-blue: #3677bd;
    --swoosh-grey: #a3a1a3;
    --ink: #1a1a1a;
    --on-blue: #ffffff;
  }
  * { box-sizing: border-box; margin: 0; padding: 0; }
  html, body {
    width: 1160px; height: 1200px; overflow: hidden;
    background: var(--backdrop);
    font-family: "Montserrat", Arial, sans-serif;
  }
  .canvas { position: relative; width: 1160px; height: 1200px; }
  .card {
    position: absolute; left: 199px; width: 777px; height: 441px;
    background: var(--card); overflow: hidden;
  }
  .card--front { top: 105px; }
  .card--back { top: 634px; }
  .wave { position: absolute; inset: 0; }
  .person { position: absolute; left: 28px; top: 64px; }
  .person__name {
    font-weight: 700; font-size: 28px; letter-spacing: -0.3px;
    color: var(--brand-blue); line-height: 1;
  }
  .person__title { margin-top: 10px; font-size: 19px; color: var(--ink); }
  .contact {
    position: absolute; left: 29px; top: 264px;
    color: var(--on-blue); font-size: 19px; line-height: 29px;
  }
  .contact__address { margin-bottom: 9px; }
  .contact__row { display: flex; align-items: center; gap: 8px; }
  .contact__icon { width: 19px; height: 19px; flex: none; }
  .brand {
    position: absolute; display: flex; align-items: center; gap: 12px;
    color: var(--brand-blue); font-weight: 700; text-transform: uppercase;
    line-height: 1.05;
  }
  .brand__mark { background: var(--brand-blue); flex: none; }
  .card--front .brand { left: 452px; top: 110px; font-size: 32px; }
  .card--front .brand__mark { width: 62px; height: 62px; }
  .card--back .brand {
    left: 50%; top: 50%; transform: translate(-50%, -50%); font-size: 44px; gap: 16px;
  }
  .card--back .brand__mark { width: 84px; height: 84px; }
</style>
</head>
<body>
<main class="canvas">
  <section class="card card--front" aria-label="Business card front">
    <svg class="wave" viewBox="0 0 777 441" width="777" height="441" aria-hidden="true">
      <path d="M0 218 C40 200 80 198 98 199 C260 195 420 340 557 373 C420 345 270 210 98 215 C60 215 30 226 0 237 Z" fill="var(--swoosh-grey)"/>
      <path d="M0 238 C40 228 70 225 98 225 C290 225 430 385 615 385 C690 385 740 365 777 350 L777 441 L0 441 Z" fill="var(--brand-blue)"/>
    </svg>
    <div class="person">
      <p class="person__name">DARA WHITFIELD</p>
      <p class="person__title">Co-Founder</p>
    </div>
    <div class="contact">
      <p class="contact__address">418 N. Harbor Lane<br>Suite 210 Marlow.12</p>
      <p class="contact__row">
        <svg class="contact__icon" viewBox="0 0 20 20" aria-hidden="true"><path d="M2 7c0-3 16-3 16 0v2h-4V7.5c-2-.8-6-.8-8 0V9H2z M5 10h10l2 7H3z" fill="#fff"/></svg>
        +254-160-42317
      </p>
      <p class="contact__row">
        <svg class="contact__icon" viewBox="0 0 20 20" aria-hidden="true"><rect x="1" y="4" width="18" height="12" fill="#fff"/><path d="M1 4l9 7 9-7" fill="none" stroke="var(--brand-blue)" stroke-width="1.5"/></svg>
        info@kestrelfac.com
      </p>
      <p class="contact__row">
        <svg class="contact__icon" viewBox="0 0 20 20" aria-hidden="true"><circle cx="10" cy="10" r="9" fill="#fff"/><path d="M4 7c2 0 3 1 3 3s2 2 2 4M12 3c0 2 2 3 4 3" fill="none" stroke="var(--brand-blue)" stroke-width="1.6"/></svg>
        www.kestrelfac.com
      </p>
    </div>
    <div class="brand"><span class="brand__mark"></span><span>Kestrel<br>Facilities</span></div>
  </section>

  <section class="card card--back" aria-label="Business card back">
    <div class="brand"><span class="brand__mark"></span><span>Kestrel<br>Facilities</span></div>
  </section>
</main>
</body>
</html>
```